Wed site for biomedical device startup

We need a generic website for a medical device startup. I will provide examples below of websites from other companies that can serve as models for what we are looking for. The startup is for a device that can non invasively measure blood flow in the brain using light. The application is to detect the type of stroke someone is having before they get to the hospital so treatment can be started right away. This saves patients upto hours of delayed treatment. Patients will be able to recover from stroke much better and faster as a result. I have attached an AI generated illustration of what the device will ultimately look like for reference.

https://www.372clinicaltech.com
https://vextalune.com

Target Market(s)

Biomedical, medical device, investors of biomedical device startups

Industry/Entity Type

Biomedical

Coding

Coded - Design and coding required

Number of Pages Required

4 page

Requirements
Must have
• same section and section headings as example websites listed above
Nice to have
• similar to example websites listed above. Prefer a darker website over a lighter one. Perhaps dark blues to go with logo colors. A moving background image element at top of landing page could be cool. Something indicative of heartbeat, or neurons, or blood flow.

```html
<!DOCTYPE html>
<html lang="en">
<head>
<meta charset="utf-8">
<title>Nevra — In Rhythm With Human Health</title>
<link href="https://fonts.googleapis.com/css2?family=Lato:wght@400;700;900&display=swap" rel="stylesheet">
<style>
  :root {
    --bg: #04041a;
    --white: #ffffff;
    --text-soft: #e4e6f2;
    --card-text: #5a5f73;
    --card-title: #1b2357;
    --purple: #7a3fd4;
    --violet: #6a4be0;
    --cyan: #27b7e8;
    --aqua: #2ec7ea;
    --rule: #2a2d4a;
  }
  * { box-sizing: border-box; margin: 0; padding: 0; }
  html, body { width: 1200px; height: 3500px; overflow: hidden; }
  body {
    background: var(--bg);
    color: var(--white);
    font-family: "Lato", sans-serif;
    position: relative;
  }
  .abs { position: absolute; }

  /* Hero */
  .hero-bg {
    left: 0; top: 0; width: 1200px; height: 690px;
    background:
      radial-gradient(ellipse 700px 520px at 900px 260px, #1d4fa8 0%, #0c2468 45%, transparent 80%),
      linear-gradient(180deg, #0b1148 0%, #070c36 60%, var(--bg) 100%);
  }
  .brand { display: flex; align-items: center; gap: 16px; }
  .brand-dot { width: 76px; height: 76px; border-radius: 50%; background: var(--violet); }
  .brand-name { font-weight: 400; letter-spacing: 3px; color: var(--white); }
  .nav { left: 554px; top: 27px; display: flex; align-items: center; }
  .nav a {
    color: var(--white); text-decoration: none; font-size: 15px;
    padding: 9px 20px; margin-right: 26px;
  }
  .nav a.active { background: var(--white); color: var(--cyan); border-radius: 20px; }
  .hero-title {
    left: 108px; top: 224px; font-size: 59px; font-weight: 900;
    line-height: 68px; letter-spacing: -0.5px;
  }
  .hero-sub { left: 112px; top: 380px; width: 470px; font-size: 19px; line-height: 30px; color: var(--text-soft); }
  .btn {
    display: inline-flex; align-items: center; justify-content: center;
    border-radius: 22px; font-weight: 700; color: var(--white); font-size: 16px;
  }
  .btn-hero { left: 111px; top: 476px; width: 178px; height: 38px; background: var(--aqua); }

  /* Plain divider bands */
  .band {
    left: 0; width: 1200px; height: 3px;
    background: linear-gradient(90deg, transparent 0%, var(--violet) 25%, var(--cyan) 75%, transparent 100%);
    opacity: 0.8;
  }

  /* Section headings */
  .heading { font-size: 40px; font-weight: 700; letter-spacing: -0.5px; }
  .heading .accent {
    background: linear-gradient(90deg, var(--purple), var(--cyan));
    -webkit-background-clip: text; background-clip: text; color: transparent;
  }
  .underline {
    width: 60px; height: 4px; border-radius: 2px;
    background: linear-gradient(90deg, var(--violet), var(--cyan));
  }

  /* About */
  .about-text { left: 111px; top: 940px; width: 436px; font-size: 15.5px; line-height: 25.8px; color: var(--text-soft); }
  .btn-read { left: 114px; top: 1169px; width: 135px; height: 38px; background: linear-gradient(90deg, var(--purple), var(--cyan)); }
  .photo-ring {
    border-radius: 50%; padding: 8px;
    background: conic-gradient(from 200deg, var(--purple), var(--cyan), var(--purple));
  }
  .photo-fill { width: 100%; height: 100%; border-radius: 50%; }

  /* Technology */
  .tech-intro { left: 280px; top: 1420px; width: 640px; text-align: center; font-size: 16px; line-height: 26px; color: var(--text-soft); }
  .card {
    width: 225px; height: 261px; top: 1506px; border-radius: 16px;
    background: var(--white); padding: 18px 14px 18px 18px;
  }
  .card.featured { background: linear-gradient(180deg, var(--cyan) 0%, var(--violet) 100%); }
  .card-icon {
    width: 62px; height: 62px; border-radius: 8px; background: #e8eaf3;
    display: flex; align-items: center; justify-content: center;
  }
  .card.featured .card-icon { background: var(--white); }
  .card-title {
    margin-top: 30px; font-size: 17px; font-weight: 700; color: var(--card-title);
    border-left: 2px solid var(--violet); padding-left: 10px; line-height: 24px;
  }
  .card.featured .card-title { color: var(--white); border-color: var(--white); }
  .card-text { margin-top: 18px; font-size: 13px; line-height: 19px; color: var(--card-text); }
  .card.featured .card-text { color: var(--white); }

  /* Partners */
  .partner {
    width: 202px; height: 124px; background: var(--white);
    display: flex; align-items: center; justify-content: center;
  }
  .partner-mark { width: 54px; height: 54px; border-radius: 50%; background: #d7dcea; }
  .partner-mark.square { border-radius: 8px; }

  /* Stay connected */
  .connect-text { left: 660px; top: 2636px; width: 410px; font-size: 15.5px; line-height: 26px; color: var(--text-soft); }
  .field {
    width: 204px; height: 43px; background: var(--white); color: #555a6a;
    font-size: 13px; padding: 0 16px; display: flex; align-items: center; border: 1px solid #d5d8e4;
  }
  .btn-sub { left: 662px; top: 2883px; width: 134px; height: 37px; background: linear-gradient(90deg, var(--purple), var(--cyan)); }

  /* Footer */
  .footer-about { left: 112px; top: 3318px; width: 410px; font-size: 15px; line-height: 22px; }
  .footer-h { font-size: 20px; font-weight: 700; }
  .footer-list { list-style: none; font-size: 15px; }
  .footer-list li { height: 31.6px; }
  .footer-rule { left: 111px; top: 3451px; width: 978px; height: 1px; background: var(--rule); }
  .copyright { left: 0; top: 3467px; width: 1200px; text-align: center; font-size: 13px; }
</style>
</head>
<body>

<!-- Hero -->
<div class="abs hero-bg"></div>
<div class="abs" role="img" aria-label="Glowing anatomical heart with a heartbeat trace across a blue body silhouette"
     style="left:620px;top:110px;width:580px;height:420px;background:radial-gradient(ellipse at 40% 50%, rgba(255,140,50,0.55), rgba(40,110,220,0.35) 45%, transparent 75%);"></div>

<header>
  <div class="abs brand" style="left:113px;top:33px;">
    <span class="brand-dot"></span>
    <span class="brand-name" style="font-size:52px;">NEVRA</span>
  </div>
  <nav class="abs nav">
    <a class="active" href="#">Home</a>
    <a href="#">About</a>
    <a href="#">Technology</a>
    <a href="#">Press</a>
    <a href="#">Contact</a>
  </nav>
</header>

<h1 class="abs hero-title">IN RHYTHM WITH<br>HUMAN HEALTH</h1>
<p class="abs hero-sub">Our heartbeat-inspired platform delivers real-time insight into vital biomedical signals.</p>
<a class="abs btn btn-hero">Connect With Us</a>

<div class="abs band" style="top:670px;"></div>

<!-- About -->
<section>
  <h2 class="abs heading" style="left:111px;top:834px;">ABOUT <span class="accent">US</span></h2>
  <div class="abs underline" style="left:112px;top:888px;"></div>
  <p class="abs about-text">Lorem ipsum dolor sit amet, consectetur adipiscing elit, sed do eiusmod tempor incididunt ut labore et dolore magna aliqua. Ut enim ad minim veniam, quis nostrud exercitation ullamco laboris nisi ut aliquip ex ea commodo consequat. Duis aute irure dolor in reprehenderit in voluptate velit esse cillum dolore eu fugiat nulla pariatur. Excepteur sint occaecat cupidatat non proident, sunt in culpa qui officia deserunt mollit anim id est laborum.</p>
  <a class="abs btn btn-read">Read More</a>
  <div class="abs photo-ring" style="left:621px;top:786px;width:466px;height:466px;">
    <div class="photo-fill" role="img" aria-label="Patient wearing forehead sensor pads while a clinician holds a monitoring device"
         style="background:linear-gradient(135deg,#e9ded4 0%,#c9a48c 50%,#5d6670 100%);"></div>
  </div>
</section>

<!-- Technology -->
<section>
  <h2 class="abs heading" style="left:0;top:1330px;width:1200px;text-align:center;">ADVANCED <span class="accent">TECHNOLOGY</span></h2>
  <div class="abs underline" style="left:570px;top:1388px;"></div>
  <p class="abs tech-intro">We combine biomedical signal capture with real-time AI analytics to deliver insights that matter — faster, smarter, and more accurately than ever before.</p>

  <div class="abs card" style="left:113px;">
    <div class="card-icon"><svg width="36" height="36" viewBox="0 0 36 36" fill="none" stroke="#6a4be0" stroke-width="1.6"><rect x="5" y="5" width="18" height="24" rx="2"/><path d="M9 11h10M9 16h8M9 21h6"/><circle cx="25" cy="23" r="6"/><path d="M29 27l4 4"/></svg></div>
    <div class="card-title">AI-Powered Diagnostic</div>
    <p class="card-text">Detect and predict critical conditions using machine learning.</p>
  </div>
  <div class="abs card featured" style="left:363px;">
    <div class="card-icon"><svg width="36" height="36" viewBox="0 0 36 36" fill="none" stroke="#6a4be0" stroke-width="1.6"><circle cx="18" cy="18" r="13"/><path d="M8 18h5l2-5 3 10 3-8 2 3h5"/></svg></div>
    <div class="card-title">Real-Time Signal Processing</div>
    <p class="card-text">Monitor heartbeat, neural, or vascular signals with instant feedback.</p>
  </div>
  <div class="abs card" style="left:612px;">
    <div class="card-icon"><svg width="36" height="36" viewBox="0 0 36 36" fill="none" stroke="#6a4be0" stroke-width="1.6"><path d="M10 22a6 6 0 0 1 1-12 8 8 0 0 1 15 2 5 5 0 0 1 0 10z"/><path d="M14 22v6M18 22v8M22 22v6"/></svg></div>
    <div class="card-title">Cloud-Based Platform</div>
    <p class="card-text">Secure and scalable infrastructure for hospitals, labs, or remote devices.</p>
  </div>
  <div class="abs card" style="left:862px;">
    <div class="card-icon"><svg width="36" height="36" viewBox="0 0 36 36" fill="none" stroke="#6a4be0" stroke-width="1.6"><rect x="8" y="8" width="20" height="20" rx="3"/><path d="M14 14h8v8h-8z"/></svg></div>
    <div class="card-title">Custom Algorithms</div>
    <p class="card-text">Excepteur sint occaecat c non proident, sunt in mollit anim id est laborum."</p>
  </div>
</section>

<div class="abs band" style="top:1892px;"></div>

<!-- Partners -->
<section>
  <h2 class="abs heading" style="left:0;top:1994px;width:1200px;text-align:center;">PARTNERS AND <span class="accent">COLLABORATORS</span></h2>
  <div class="abs underline" style="left:570px;top:2052px;"></div>

  <div class="abs partner" style="left:111px;top:2116px;"><span class="partner-mark"></span></div>
  <div class="abs partner" style="left:370px;top:2116px;"><span class="partner-mark square"></span></div>
  <div class="abs partner" style="left:628px;top:2116px;"><span class="partner-mark"></span></div>
  <div class="abs partner" style="left:886px;top:2116px;"><span class="partner-mark square"></span></div>
  <div class="abs partner" style="left:111px;top:2287px;"><span class="partner-mark square"></span></div>
  <div class="abs partner" style="left:370px;top:2287px;"><span class="partner-mark"></span></div>
  <div class="abs partner" style="left:628px;top:2287px;"><span class="partner-mark square"></span></div>
  <div class="abs partner" style="left:886px;top:2287px;"><span class="partner-mark"></span></div>
</section>

<!-- Stay connected -->
<section>
  <div class="abs photo-ring" style="left:113px;top:2497px;width:467px;height:467px;">
    <div class="photo-fill" role="img" aria-label="Close-up of red blood cells flowing in a vessel"
         style="background:radial-gradient(circle at 45% 45%, #d8403a 0%, #a81d22 55%, #5a0c12 100%);"></div>
  </div>
  <h2 class="abs heading" style="left:660px;top:2534px;">STAY <span class="accent">CONNECTED</span></h2>
  <div class="abs underline" style="left:662px;top:2590px;"></div>
  <p class="abs connect-text">Join our community to receive updates about our latest developments and research in blood loss monitoring technology.</p>
  <form>
    <div class="abs field" style="left:662px;top:2745px;">First Name</div>
    <div class="abs field" style="left:885px;top:2745px;">Last Name</div>
    <div class="abs field" style="left:662px;top:2807px;">Email</div>
    <div class="abs field" style="left:885px;top:2807px;">Company</div>
    <a class="abs btn btn-sub">Subscribe</a>
  </form>
</section>

<div class="abs band" style="top:3078px;"></div>

<!-- Footer -->
<footer>
  <div class="abs brand" style="left:113px;top:3196px;gap:20px;">
    <span class="brand-dot" style="width:98px;height:98px;"></span>
    <span class="brand-name" style="font-size:64px;">NEVRA</span>
  </div>
  <p class="abs footer-about">We are a team of scientists, engineers, and innovators dedicated to transforming how the world understands and interacts with the human body.</p>

  <h3 class="abs footer-h" style="left:648px;top:3186px;">Main Links</h3>
  <ul class="abs footer-list" style="left:648px;top:3231px;">
    <li>Home</li><li>About</li><li>Technology</li><li>Press</li><li>Contact</li>
  </ul>

  <h3 class="abs footer-h" style="left:900px;top:3186px;">Contact</h3>
  <p class="abs" style="left:900px;top:3231px;width:200px;font-size:15px;line-height:23px;">48 Lumen Park, Suite 9, Ardell 40218</p>
  <p class="abs" style="left:900px;top:3305px;font-size:15px;">hello@nevra-neuro.com</p>
  <p class="abs" style="left:900px;top:3351px;font-size:15px;">+1 555 014 2290</p>

  <div class="abs footer-rule"></div>
  <p class="abs copyright">2025 Nevra. All rights reserved.</p>
</footer>

</body>
</html>
```